Business Card Design Project

Looking to update our business cards. We have a logo with our slogan. We are an IT firm so we wouldlike a modern look.

Industry/Entity Type

Business

```html
<!DOCTYPE html>
<html lang="en">
<head>
<meta charset="utf-8">
<title>Nexabyte Business Cards</title>
<link href="https://fonts.googleapis.com/css2?family=Jost:ital,wght@0,400;0,500;0,600;1,600&display=swap" rel="stylesheet">
<style>
  :root {
    --stage: #ece8e3;
    --label: #2a2522;
    --brand-green: #6b8a3a;
    --brand-lime: #a9c23f;
    --ink: #1c1c1c;
    --white: #ffffff;
    --silver-light: #e4e4e4;
    --silver-mid: #a9a9a9;
    --graphite-dark: #1e1e1e;
    --graphite-mid: #5a5a5a;
    --tech-deep: #0f1f6e;
    --tech-mid: #3a6fd8;
    --tech-glow: #e8f2ff;
  }
  * { margin: 0; padding: 0; box-sizing: border-box; }
  html, body { width: 1200px; height: 788px; overflow: hidden; }
  body {
    position: relative;
    background: var(--stage);
    font-family: "Jost", "Futura", sans-serif;
  }
  .view-label {
    position: absolute;
    width: 525px;
    text-align: center;
    font-size: 22px;
    font-weight: 400;
    color: var(--label);
  }
  .card {
    position: absolute;
    width: 525px;
    height: 298px;
    border-radius: 22px;
    overflow: hidden;
  }
  .card--front { left: 52px; top: 82px;
    background: linear-gradient(180deg, var(--silver-light) 0%, #c9c9c9 45%, var(--silver-mid) 70%, #3a3a3a 100%); }
  .card--plain { left: 620px; top: 80px; background: var(--white); }
  .card--graphite { left: 48px; top: 454px;
    background: linear-gradient(100deg, var(--graphite-dark) 0%, var(--graphite-mid) 55%, #3d3d3d 100%); }
  .card--tech { left: 620px; top: 454px;
    background: radial-gradient(ellipse at 50% 55%, var(--tech-glow) 0%, #9fc2f5 22%, var(--tech-mid) 50%, var(--tech-deep) 100%); }

  .brand {
    position: absolute;
    left: 0; right: 0;
    display: flex;
    flex-direction: column;
    align-items: center;
  }
  .brand__name {
    display: flex;
    align-items: center;
    gap: 10px;
    font-weight: 600;
    color: var(--brand-green);
    letter-spacing: 4px;
    line-height: 1;
  }
  .brand__dot {
    display: inline-block;
    border-radius: 50%;
    background: var(--brand-lime);
  }
  .brand__tagline {
    font-weight: 600;
    color: var(--ink);
    letter-spacing: 3px;
    line-height: 1;
  }
  .card--front .brand { top: 46px; }
  .card--front .brand__name { font-size: 40px; }
  .card--front .brand__dot { width: 14px; height: 14px; }
  .card--front .brand__tagline { font-size: 11px; margin-top: 8px; letter-spacing: 2.5px; }

  .card--plain .brand,
  .card--graphite .brand,
  .card--tech .brand { top: 112px; }
  .card--plain .brand__name,
  .card--graphite .brand__name,
  .card--tech .brand__name { font-size: 50px; }
  .card--plain .brand__dot,
  .card--graphite .brand__dot,
  .card--tech .brand__dot { width: 16px; height: 16px; }
  .card--plain .brand__tagline,
  .card--graphite .brand__tagline,
  .card--tech .brand__tagline { font-size: 13px; margin-top: 12px; }

  .contact { position: absolute; left: 0; right: 0; color: var(--white); }
  .contact__person { top: 168px; text-align: center; font-size: 18px; font-weight: 600; }
  .contact__role { font-size: 13px; font-weight: 400; }
  .contact__grid {
    top: 208px;
    display: grid;
    grid-template-columns: 170px 1px 190px;
    column-gap: 10px;
    justify-content: center;
    font-size: 13px;
    line-height: 18px;
  }
  .contact__col--left { text-align: right; }
  .contact__divider { background: var(--white); }
  .contact__key { font-style: italic; font-weight: 600; }
  .contact__address { top: 258px; text-align: center; font-size: 13px; }

  .stripe { position: absolute; left: 0; bottom: 0; width: 100%; height: 12px; display: flex; }
  .stripe__green { width: 158px; background: var(--brand-green); }
  .stripe__black { width: 207px; background: #000; }
  .stripe__lime { flex: 1; background: var(--brand-lime); }

  .tech-art { position: absolute; inset: 0; }
</style>
</head>
<body>
  <div class="view-label" style="left:52px; top:34px;">Front</div>
  <div class="view-label" style="left:620px; top:34px;">Back - 1</div>
  <div class="view-label" style="left:48px; top:404px;">Back - 2</div>
  <div class="view-label" style="left:620px; top:404px;">Back - 3</div>

  <section class="card card--front">
    <div class="brand">
      <div class="brand__name"><span>NEXABYTE</span><span class="brand__dot"></span></div>
      <div class="brand__tagline">SMART SYSTEMS MADE EASY</div>
    </div>
    <div class="contact contact__person">Your Name, <span class="contact__role">Designation</span></div>
    <div class="contact contact__grid">
      <div class="contact__col--left">
        <div><span class="contact__key">phone</span> : +12 345 67890</div>
        <div><span class="contact__key">fax</span> : +12 345 67890</div>
      </div>
      <div class="contact__divider"></div>
      <div>
        <div><span class="contact__key">email</span> : info@website.com</div>
        <div><span class="contact__key">web</span> : www.website.com</div>
      </div>
    </div>
    <div class="contact contact__address">#0000, Street Name, Area Name, Country Code</div>
    <div class="stripe"><span class="stripe__green"></span><span class="stripe__black"></span><span class="stripe__lime"></span></div>
  </section>

  <section class="card card--plain">
    <div class="brand">
      <div class="brand__name"><span>NEXABYTE</span><span class="brand__dot"></span></div>
      <div class="brand__tagline">SMART SYSTEMS MADE EASY</div>
    </div>
  </section>

  <section class="card card--graphite">
    <div class="brand">
      <div class="brand__name"><span>NEXABYTE</span><span class="brand__dot"></span></div>
      <div class="brand__tagline">SMART SYSTEMS MADE EASY</div>
    </div>
  </section>

  <section class="card card--tech">
    <div class="tech-art" role="img" aria-label="Abstract blue technology illustration with glowing light rings, binary digits and a wireframe globe"></div>
    <div class="brand">
      <div class="brand__name"><span>NEXABYTE</span><span class="brand__dot"></span></div>
      <div class="brand__tagline">SMART SYSTEMS MADE EASY</div>
    </div>
  </section>
</body>
</html>
```